Business card design for a teacher - double sided, sleek design.

My name is Lina and I am an online Arabic language teacher. I am looking for a beautiful business card design for my online teaching business.

The cards will be printed in 85mm x 55mm size.
The card can be either portrait or landscape.

The design should contain my logo on one side and information on the other.

The design needs to be clean and modern. Use of subtle Arabic geometric patterns would be nice. Icons for the social media information on the card should also match the design theme.

My logo font is Consolas, which is a Monospace font.

Business card design should be delivered with editable PSD or EPS files in the handover.

Thanks

Lina

----

Information on the back:

URL: www.speakwithnadia.net [this should stand out more than other details]
Email: info@speakwithnadia.net
Instagram: @speakwithnadia
Facebook: facebook.com/speakwithnadia
Skype: speakwithnadia

My brand colours are shown in the logo attached. These are:
- Teal green - 4DC9C1
- Mango yellow - FFD600

Target Market(s)

- Young professionals
- Expatriates
- Women and Men

Industry/Entity Type

Education

Contact Information for Business Card

Information on the back:

Skype: speakwithnadia

- Teal green - 4DC9C1
- Mango yellow - FFD600

Font styles to use
Other font styles liked:
• Any font complimentary to my logo font which is a Monospace font called Consolas.

Colors

Designer to choose colors to be used in the design.

Requirements
Must have
• - Aesthetically pleasing look
• - Complimentary design with existing logo
Nice to have
• Arabic geometrical patterns

```html
<!DOCTYPE html>
<html lang="en">
<head>
<meta charset="utf-8">
<title>Arabic with Lina — Business Card</title>
<link href="https://fonts.googleapis.com/css2?family=Open+Sans:wght@400;600&family=Source+Code+Pro:wght@500&display=swap" rel="stylesheet">
<style>
  :root {
    --teal: #57c5be;
    --teal-deep: #4dc9c1;
    --mango: #ffd600;
    --white: #ffffff;
    --ink: #4a4a4a;
    --pattern: #eef8f6;
    --backdrop: #1e1e1e;
  }
  * { margin: 0; padding: 0; box-sizing: border-box; }
  html, body { width: 1200px; height: 960px; overflow: hidden; }
  body { background: var(--backdrop); position: relative; font-family: "Open Sans", Arial, sans-serif; }

  .card { position: absolute; width: 600px; height: 342px; overflow: hidden; }
  .card--front { left: 314px; top: 113px; background: var(--teal); }
  .card--back  { left: 311px; top: 472px; background: var(--white); }

  .card__art { position: absolute; inset: 0; }

  .brand { position: absolute; left: 41px; top: 50px; display: flex; align-items: center; gap: 16px; }
  .brand__square { width: 79px; height: 82px; border: 2px solid var(--white); }
  .brand__name {
    font-family: "Source Code Pro", Consolas, monospace; font-weight: 500;
    color: var(--white); line-height: 1; text-transform: uppercase;
  }
  .brand__name span { display: block; }
  .brand__name .lg { font-size: 30px; letter-spacing: 2px; }
  .brand__name .sm { font-size: 9px; letter-spacing: 2px; margin: 6px 0 6px 50px; }

  .contacts { position: absolute; left: 40px; top: 206px; list-style: none; }
  .contacts li {
    display: flex; align-items: center; gap: 8px; height: 19px;
    font-size: 13px; color: var(--white);
  }
  .contacts svg { width: 13px; height: 13px; flex: none; }

  .back-logo {
    position: absolute; left: 217px; top: 79px; width: 162px; height: 171px;
    border: 4px solid var(--mango);
    display: flex; align-items: center; justify-content: center;
  }
  .back-logo__name {
    font-family: "Source Code Pro", Consolas, monospace; font-weight: 500;
    color: var(--teal-deep); text-align: center; line-height: 1.25;
    font-size: 20px; letter-spacing: 4px; text-transform: uppercase;
  }
  .back-url {
    position: absolute; left: 0; right: 0; top: 293px; text-align: center;
    font-family: "Source Code Pro", Consolas, monospace; font-weight: 500;
    font-size: 14px; letter-spacing: 5px; color: var(--ink); text-transform: uppercase;
  }
</style>
</head>
<body>

<section class="card card--front" aria-label="Business card front">
  <svg class="card__art" viewBox="0 0 600 342" aria-hidden="true">
    <path d="M356 0 C330 60 300 110 268 150 C228 200 236 262 292 300 C334 326 392 342 432 342 L600 342 L600 0 Z" fill="var(--mango)"/>
    <path d="M354 18 L17 18 L17 328 L458 328" fill="none" stroke="var(--white)" stroke-width="2.5"/>
    <rect x="253" y="323" width="9" height="9" transform="rotate(45 257.5 327.5)" fill="var(--mango)"/>
    <rect x="273" y="323" width="9" height="9" transform="rotate(45 277.5 327.5)" fill="var(--mango)"/>
  </svg>

  <div class="brand">
    <div class="brand__square"></div>
    <div class="brand__name">
      <span class="lg">Arabic</span>
      <span class="sm">with</span>
      <span class="lg">Lina</span>
    </div>
  </div>

  <ul class="contacts">
    <li>
      <svg viewBox="0 0 13 13"><rect x="0.5" y="2.5" width="12" height="8" fill="var(--mango)"/><path d="M0.5 2.5 L6.5 7 L12.5 2.5" fill="none" stroke="var(--teal)" stroke-width="1.2"/></svg>
      info@speakwithnadia.net
    </li>
    <li>
      <svg viewBox="0 0 13 13"><rect x="1" y="1" width="11" height="11" fill="var(--mango)"/></svg>
      @speakwithnadia
    </li>
    <li>
      <svg viewBox="0 0 13 13"><rect x="1" y="1" width="11" height="11" fill="var(--mango)"/></svg>
      speakwithnadia
    </li>
    <li>
      <svg viewBox="0 0 13 13"><circle cx="6.5" cy="6.5" r="5.5" fill="var(--mango)"/></svg>
      speakwithnadia
    </li>
    <li>
      <svg viewBox="0 0 13 13"><circle cx="6.5" cy="6.5" r="5.5" fill="none" stroke="var(--mango)" stroke-width="1.6"/><path d="M1 6.5 H12 M6.5 1 C3.5 4 3.5 9 6.5 12 C9.5 9 9.5 4 6.5 1" fill="none" stroke="var(--mango)" stroke-width="1.2"/></svg>
      www.speakwithnadia.net
    </li>
  </ul>
</section>

<section class="card card--back" aria-label="Business card back">
  <svg class="card__art" viewBox="0 0 600 342" role="img" aria-label="Subtle repeating light teal and yellow Arabic pattern background">
    <rect width="600" height="342" fill="var(--pattern)"/>
  </svg>
  <div class="back-logo">
    <div class="back-logo__name">Arabic<br>with<br>Lina</div>
  </div>
  <p class="back-url">www.speakwithnadia.net</p>
</section>

</body>
</html>
```